Brenvik Systems PowerPoint Template

Project Title: Professional & Functional PowerPoint Template (.potx) – Brenvik Systems Rebrand

Project Overview:
Brenvik Systems has recently undergone a complete rebranding, including a new logo, website, and visual identity. We need a professional, high-end PowerPoint Template (.potx) that reflects our new look while being highly functional for everyday use.

We previously had a design created, but it was built incorrectly (static images, oversized file, no Master Slides). The goal of this project is to take our new aesthetic and build a "workable" template where layouts are controlled by Master Slides and text is easily editable.

Style & Brand Direction:
The template must be an extension of our new website: https://www.brenvik-systems.example/

Aesthetic: Modern, clean, high-tech, and "Industrial Tech."

Color Palette: Please pull the primary blues, greys, and accent colors directly from the website.

Imagery/Graphics: Use clean lines and subtle tech-inspired gradients. Avoid "clutter."

Tone: Innovative, precise, and professional.

Technical Requirements (Crucial)
Format: Must be delivered as a PowerPoint Template file (** .potx **).

Functionality: All layouts must be built using Slide Masters. Users should be able to click "New Slide" and choose from specific layouts.

Native Elements: Do NOT use full-page background images for text areas. Bullet points must use native PowerPoint list functionality (not individual text boxes).

File Size: The template must be optimized and lightweight.

Fonts: Use standard professional fonts or provide the specific web-safe equivalent used on our site (e.g., Montserrat, Open Sans, etc.).

Required Slide Layouts
Please include a minimum of 10–12 Master layouts, including:
*Title Slide (2-3 variations: Dark and Light)
*Agenda/Table of Contents
*Section Header/Divider Slides
*Standard Text/Bullet Slide
*Two-Column Text Slide
*Image + Text Layouts (Left/Right variations)
*Data/Chart Slide (Styled bar/pie charts that match the brand)
*Process/Timeline Slide (Infographic style)
*Section slide

Attachments Provided
Brand Assets (.zip): Contains our new logo in various formats.

Inspiration/Existing PPT: We have attached the previous design created by our web agency. Note: Use this for visual inspiration ONLY. Do not copy the file structure, as it is technically flawed.

Deliverables
Final .potx file.

All used icons or custom graphics in vector format (if applicable).

Instruction note on any specific fonts used.

Target Market(s)

Internal communication and external (investors, customers)

Industry/Entity Type

Semiconductor, Automotive

Requirements
Must have
• A potx file

```html
<!DOCTYPE html>
<html lang="en">
<head>
<meta charset="utf-8">
<title>Brenvik Systems – Presentation Template Overview</title>
<link href="https://fonts.googleapis.com/css2?family=Montserrat:wght@400;500;600;700&display=swap" rel="stylesheet">
<style>
:root{
  --canvas:#d4d4d0;
  --ink:#0e0e10;
  --ink-2:#1a1b1f;
  --white:#ffffff;
  --paper:#f3f3f3;
  --blue:#1f3fe6;
  --blue-soft:#6f86ff;
  --grey-title:#4a4a4d;
  --grey-text:#77777b;
  --line:#c9c9cc;
}
*{margin:0;padding:0;box-sizing:border-box}
html,body{width:1200px;height:1047px;overflow:hidden;background:var(--canvas)}
body{position:relative;font-family:"Montserrat",Arial,sans-serif;color:var(--ink)}
.slide{position:absolute;width:282px;height:157px;overflow:hidden;background:var(--white)}
.slide.dark{background:var(--ink);color:#fff}
.a{position:absolute}
.c1{left:26px}.c2{left:314px}.c3{left:603px}.c4{left:890px}
.r1{top:22px}.r2{top:186px}.r3{top:349px}.r4{top:513px}.r5{top:677px}.r6{top:841px}
.photo{position:absolute}
.tiny{font-size:2.6px;line-height:1.5;color:var(--grey-text)}
.dark .tiny{color:#b9b9bd}
.kicker{font-size:2.8px;color:var(--blue);font-weight:600;line-height:1.2}
.desc{font-size:3.2px;font-style:italic;color:#555}
.dark .desc{color:#ccc}
.title{font-weight:600;line-height:1.12;color:var(--grey-title);letter-spacing:.2px}
.dark .title{color:#fff}
.mark{display:inline-flex;align-items:center;gap:1.5px;font-weight:700;letter-spacing:.2px}
.mark i{display:inline-block;background:var(--blue)}
.foot{position:absolute;left:22px;right:30px;top:142px;height:8px;border-top:.5px solid var(--line);font-size:2.6px;color:var(--grey-text)}
.dark .foot{border-color:#333;color:#bbb}
.foot .l{position:absolute;left:0;top:2px}
.foot .r{position:absolute;right:0;top:2px}
.foot .mark{position:absolute;left:50%;top:1.5px;transform:translateX(-50%);font-size:5px;color:var(--ink)}
.dark .foot .mark{color:#fff}
.foot .mark i{width:4px;height:4px}
.pnum{position:absolute;left:261px;top:137px;width:12px;height:12px;border-radius:50%;background:var(--blue);border:1.5px solid #9fb0ff;color:#fff;font-size:3px;display:flex;align-items:center;justify-content:center}
.num{display:inline-flex;width:6px;height:6px;border-radius:50%;background:var(--blue);color:#fff;font-size:2.6px;align-items:center;justify-content:center}
.item-t{font-size:3.4px;letter-spacing:.3px;color:#555;margin-top:3px}
.dark .item-t{color:#ddd}
.arrowline{position:absolute;height:10px}
.cols p{margin-bottom:2.5px}
</style>
</head>
<body>

<!-- 1 Cover logo -->
<section class="slide c1 r1">
  <div class="a mark" style="left:36px;top:56px;font-size:31px;gap:9px;color:var(--ink)"><i style="width:41px;height:41px"></i>BRENVIK</div>
  <div class="pnum">1</div>
</section>

<!-- 2 Cover blue -->
<section class="slide dark c2 r1">
  <div class="a" style="left:9px;top:9px;width:166px;height:139px;background:var(--blue)"></div>
  <div class="a tiny" style="left:29px;top:20px;color:#fff">PowerPoint<br>Template</div>
  <div class="a" style="left:65px;top:19px;width:79px;height:5px;border:.5px solid #fff;font-size:2.4px;padding-left:2px;color:#fff;font-weight:600">Another Title Goes Here</div>
  <div class="a mark" style="left:33px;top:38px;font-size:10px;color:#fff"><i style="width:9px;height:9px;background:#fff"></i>BRENVIK</div>
  <div class="a" style="left:33px;top:60px;font-size:20px;font-weight:700;line-height:1.08;color:#fff">Brenvik<br>Systems</div>
  <div class="a" style="left:120px;top:117px;font-size:7px;color:#fff">2026</div>
  <svg class="a" style="left:28px;top:125px" width="140" height="16"><circle cx="8" cy="8" r="7" fill="none" stroke="#fff" stroke-width=".6"/><line x1="8" y1="8" x2="138" y2="8" stroke="#fff" stroke-width=".5"/><path d="M135 6.5 138 8 135 9.5" fill="none" stroke="#fff" stroke-width=".5"/></svg>
  <div class="a" style="left:197px;top:9px;width:75px;height:110px;border:.5px solid #2b40b8"></div>
  <div class="photo" role="img" aria-label="Close-up of a precision nozzle above a silicon wafer, lit in blue" style="left:181px;top:23px;width:79px;height:111px;background:radial-gradient(circle at 45% 60%,#5d7aff 0,#1c2a6e 25%,#0a0d1c 70%)"></div>
  <div class="a tiny" style="left:182px;top:137px">@brenviksite</div>
</section>

<!-- 3 Cover light -->
<section class="slide c3 r1">
  <div class="photo" role="img" aria-label="Stacked translucent glass plates on a diagonal" style="left:150px;top:0;width:132px;height:157px;background:linear-gradient(135deg,#fff 10%,#b9c7c6 40%,#3a4446 60%,#c7d3d2 80%,#fff)"></div>
  <div class="a tiny" style="left:24px;top:11px;color:#333">Mar 20th, 2026<br><b>Your Company</b></div>
  <div class="a tiny" style="left:130px;top:11px;color:#333">Brenvik<br><b>Presentation</b></div>
  <div class="a mark" style="left:26px;top:33px;font-size:10px;color:var(--ink)"><i style="width:9px;height:9px"></i>BRENVIK</div>
  <div class="a" style="left:26px;top:55px;font-size:15px;font-weight:700">Brenvik <span style="color:var(--blue)">Systems</span></div>
  <svg class="a" style="left:24px;top:87px" width="95" height="20"><circle cx="10" cy="10" r="9" fill="none" stroke="#666" stroke-width=".5"/><line x1="10" y1="10" x2="93" y2="10" stroke="#555" stroke-width=".5"/><path d="M90 8.5 93 10 90 11.5" fill="none" stroke="#555" stroke-width=".5"/></svg>
  <div class="a" style="left:27px;top:112px;font-size:3.2px;letter-spacing:1px;color:#444">PRESENTATION TEMPLATE</div>
  <div class="a tiny" style="left:26px;top:128px;color:#333">Presented by<br><b>Ansel Kroft</b></div>
  <svg class="a" style="left:130px;top:125px" width="14" height="14"><circle cx="7" cy="7" r="6" fill="none" stroke="#999" stroke-width=".6"/><line x1="1" y1="7" x2="13" y2="7" stroke="#999" stroke-width=".6"/><line x1="7" y1="1" x2="7" y2="13" stroke="#999" stroke-width=".6"/></svg>
</section>

<!-- 4 Contents -->
<section class="slide dark c4 r1">
  <div class="photo" role="img" aria-label="Fine line technical drawing of a dispensing machine" style="left:175px;top:0;width:107px;height:140px;background:linear-gradient(180deg,#1a1a1d,#111113);border-left:.5px solid #2a2a2e"></div>
  <div class="a tiny" style="left:122px;top:12px;color:#fff;text-decoration:underline">Brenvik Systems Rebrand</div>
  <div class="a" style="left:19px;top:33px;font-size:14px;letter-spacing:.5px">CONTENTS</div>
  <div class="a tiny" style="left:22px;top:66px;line-height:2.2;color:#aaa">01&nbsp;&nbsp;ABOUT ME<br>02&nbsp;&nbsp;TECHNICAL SKILLS<br>03&nbsp;&nbsp;PERSONAL SKILLS<br>04&nbsp;&nbsp;EDUCATION BACKGROUND<br>05&nbsp;&nbsp;WORK EXPERIENCE<br>06&nbsp;&nbsp;VOLUNTEER WORK<br>07&nbsp;&nbsp;NOTABLE ACHIEVEMENTS</div>
  <div class="a tiny" style="left:105px;top:66px;line-height:2.2;color:#aaa">08&nbsp;&nbsp;HOBBIES AND INTEREST<br>09&nbsp;&nbsp;STRENGTHS<br>10&nbsp;&nbsp;CERTIFICATES<br>11&nbsp;&nbsp;PORTFOLIO<br>12&nbsp;&nbsp;CLIENTS<br>13&nbsp;&nbsp;CONTACT INFORMATION</div>
  <div class="foot"><span class="l">ACCOUNTANT</span><span class="mark"><i></i>BRENVIK</span><span class="r">PETRA LUND</span></div>
  <div class="pnum">4</div>
</section>

<!-- 5 Agenda -->
<section class="slide c1 r2" style="background:var(--paper)">
  <div class="a" style="left:-20px;top:-30px;width:210px;height:210px;border-radius:50%;background:#eaeaea"></div>
  <div class="photo" role="img" aria-label="Silver dispensing needle above a wafer on a white block" style="left:5px;top:8px;width:125px;height:125px;border-radius:50%;background:radial-gradient(circle at 50% 40%,#fff,#d9dadc 55%,#b8babd)"></div>
  <div class="a tiny" style="left:153px;top:44px;color:#aaa">Our Agenda</div>
  <div class="a" style="left:153px;top:50px;font-size:9px;font-weight:600;letter-spacing:.5px">Agenda.</div>
  <div class="a" style="left:153px;top:62px;width:41px;height:1.3px;background:var(--blue)"></div>
  <div class="a tiny" style="left:155px;top:75px;line-height:2.6;color:#333">•&nbsp;&nbsp;Our Company<br>•&nbsp;&nbsp;Our Team<br>•&nbsp;&nbsp;Our Portfolio<br>•&nbsp;&nbsp;Coffee Breaks<br>•&nbsp;&nbsp;Timeline</div>
  <div class="a tiny" style="left:204px;top:75px;line-height:2.6;color:#333">•&nbsp;&nbsp;Charts<br>•&nbsp;&nbsp;Product Overview<br>•&nbsp;&nbsp;Maps<br>•&nbsp;&nbsp;Contact Us</div>
  <div class="foot"><span class="l">Brenvik Systems</span><span class="mark"><i></i>BRENVIK</span><span class="r">Presentation</span></div>
  <div class="pnum">5</div>
</section>

<!-- 6 Section break -->
<section class="slide dark c2 r2">
  <div class="photo" role="img" aria-label="Dark industrial dispensing machine over a wafer" style="left:0;top:0;width:282px;height:157px;background:radial-gradient(circle at 30% 60%,#3a3d44,#15161a 55%,#0b0b0d)"></div>
  <div class="a" style="left:271px;top:0;width:11px;height:22px;background:var(--blue)"></div>
  <div class="a" style="left:0;top:14px;width:110px;height:.5px;background:#2d45c8"></div>
  <div class="a" style="left:140px;top:22px;font-size:16px;font-weight:700;line-height:1.05">SECTION<br>BREAK</div>
  <div class="a tiny" style="left:142px;top:62px;width:62px;color:#ccc">A wonderful serenity has taken of my entire soul, like these sweet mornings of spring which I enjoy with my whole heart. I am alone,</div>
  <div class="a" style="left:173px;top:90px;font-size:5px;color:var(--blue-soft)">→&nbsp;&nbsp;Next slide</div>
  <div class="foot"><span class="l" style="color:#fff">Brenvik Systems</span><span class="mark"><i></i>BRENVIK</span><span class="r" style="color:#fff">Presentation</span></div>
  <div class="pnum">6</div>
</section>

<!-- 7 Purpose list -->
<section class="slide c3 r2">
  <div class="a kicker" style="left:30px;top:11px">Vision and<br>Missions</div>
  <div class="a desc" style="left:30px;top:25px">Description here</div>
  <div class="a title" style="left:30px;top:33px;font-size:15px">PURPOSE<br>&amp; GOALS</div>
  <div class="a tiny" style="left:30px;top:74px;width:82px">A wonderful serenity has taken of my entire soul, like these sweet mornings of spring which I enjoy with my whole heart. I am alone, and feel the charm of existence in this spot, which was<br><br>created for the bliss of souls like mine. I am so happy, my dear friend, so absorbed in the exquisite</div>
  <svg class="a" style="left:6px;top:45px" width="18" height="80"><line x1="9" y1="2" x2="9" y2="70" stroke="#666" stroke-width=".5"/><path d="M7.5 5 9 2 10.5 5" fill="none" stroke="#666" stroke-width=".5"/><circle cx="9" cy="70" r="8" fill="none" stroke="#666" stroke-width=".5"/></svg>
  <div class="a" style="left:125px;top:30px;width:2px;height:2px;background:#333"></div>
  <div class="a" style="left:130px;top:32px;width:127px">
    <div style="height:25px;border-bottom:.5px solid #ccc;display:flex;justify-content:space-between"><div><div style="font-size:4.6px;color:var(--blue)">Dark theme</div><div class="tiny">A wonderful serenity has</div></div><div class="tiny" style="width:60px">A wonderful serenity has taken of my entire soul, like these mornings</div></div>
    <div style="height:25px;border-bottom:.5px solid #ccc;display:flex;justify-content:space-between;padding-top:4px"><div><div style="font-size:4.6px;color:var(--blue)">Trend design</div><div class="tiny">A wonderful serenity has</div></div><div class="tiny" style="width:60px">A wonderful serenity has taken of my entire soul, like these mornings</div></div>
    <div style="height:25px;border-bottom:.5px solid #ccc;display:flex;justify-content:space-between;padding-top:4px"><div><div style="font-size:4.6px;color:var(--blue)">Elegant design</div><div class="tiny">A wonderful serenity has</div></div><div class="tiny" style="width:60px">A wonderful serenity has taken of my entire soul, like these mornings</div></div>
    <div style="height:25px;display:flex;justify-content:space-between;padding-top:4px"><div><div style="font-size:4.6px;color:var(--blue)">2020 trend</div><div class="tiny">A wonderful serenity has</div></div><div class="tiny" style="width:60px">A wonderful serenity has taken of my entire soul, like these mornings</div></div>
  </div>
  <div class="foot"><span class="l">Brenvik Systems</span><span class="mark"><i></i>BRENVIK</span><span class="r">Presentation</span></div>
  <div class="pnum">7</div>
</section>

<!-- 8 Services icons -->
<section class="slide dark c4 r2">
  <div class="photo" role="img" aria-label="Dispensing machine head over a wafer" style="left:140px;top:0;width:142px;height:45px;background:linear-gradient(90deg,#0e0e10,#2c2e33 50%,#0e0e10)"></div>
  <div class="a kicker" style="left:30px;top:11px">Services</div>
  <div class="a" style="left:30px;top:29px;font-size:15px;font-weight:600">SERVICES</div>
  <div class="a tiny" style="left:31px;top:75px;width:72px">A wonderful serenity has taken of my entire soul, like these sweet mornings of spring which I enjoy with my whole heart. I am alone, and feel the charm of existence in this spot, which was<br><br>created for the bliss of souls like mine. I am so happy, my dear friend, so absorbed in the exquisite</div>
  <div class="a" style="left:118px;top:75px;width:150px;display:grid;grid-template-columns:1fr 1fr;row-gap:17px">
    <div style="display:flex;gap:4px"><span style="width:18px;height:18px;background:var(--blue)"></span><div><div style="font-size:4.6px;color:var(--blue-soft)">Strategy</div><div class="tiny">A wonderful serenity has</div></div></div>
    <div style="display:flex;gap:4px"><span style="width:18px;height:18px;background:var(--blue)"></span><div><div style="font-size:4.6px;color:var(--blue-soft)">Night light</div><div class="tiny">A wonderful serenity has</div></div></div>
    <div style="display:flex;gap:4px"><span style="width:18px;height:18px;background:var(--blue)"></span><div><div style="font-size:4.6px;color:var(--blue-soft)">Security</div><div class="tiny">A wonderful serenity has</div></div></div>
    <div style="display:flex;gap:4px"><span style="width:18px;height:18px;background:var(--blue)"></span><div><div style="font-size:4.6px;color:var(--blue-soft)">Ambient</div><div class="tiny">A wonderful serenity has</div></div></div>
  </div>
  <div class="a" style="left:0;top:146px;width:12px;height:11px;background:var(--blue)"></div>
  <div class="foot"><span class="l" style="color:#fff">Brenvik Systems</span><span class="mark"><i></i>BRENVIK</span><span class="r" style="color:#fff">Presentation</span></div>
  <div class="pnum">8</div>
</section>

<!-- 9 Two column text -->
<section class="slide c1 r3">
  <div class="a" style="left:0;top:0;width:125px;height:157px;background:#f4f4f4"></div>
  <div class="a kicker" style="left:25px;top:37px">Vision and<br>Missions</div>
  <div class="a desc" style="left:25px;top:51px">Description here</div>
  <div class="a title" style="left:25px;top:60px;font-size:15px">PURPOSE<br>&amp; GOALS</div>
  <svg class="a" style="left:13px;top:108px" width="95" height="20"><circle cx="10" cy="10" r="9" fill="none" stroke="#666" stroke-width=".5"/><line x1="10" y1="10" x2="93" y2="10" stroke="#555" stroke-width=".5"/><path d="M90 8.5 93 10 90 11.5" fill="none" stroke="#555" stroke-width=".5"/></svg>
  <div class="a tiny cols" style="left:136px;top:14px;width:64px;color:#333"><p>A wonderful serenity has taken of my entire soul, like these sweet mornings of spring which I enjoy with my whole heart. I am alone, and feel the charm of existence in this spot, which was</p><p>created for the bliss of souls like mine. I am so happy, my dear friend, so absorbed in the exquisite</p><p>created for the bliss of souls like mine. I am so happy, my dear friend, so absorbed in the exquisite created for the bliss of souls like mine. I am so happy, my dear friend, so absorbed in the exquisite</p></div>
  <div class="a tiny cols" style="left:205px;top:14px;width:64px;color:#333"><p>A wonderful serenity has taken of my entire soul, like these sweet mornings of spring which I enjoy with my whole heart. I am alone, and feel the charm of existence in this spot, which was</p><p>created for the bliss of souls like mine. I am so happy, my dear friend, so absorbed in the exquisite</p><p>created for the bliss of souls like mine. I am so happy, my dear friend, so absorbed in the exquisite created for the bliss of souls like mine. I am so happy, my dear friend, so absorbed in the exquisite</p></div>
  <div class="foot"><span class="l">Brenvik Systems</span><span class="mark"><i></i>BRENVIK</span><span class="r">Presentation</span></div>
  <div class="pnum">9</div>
</section>

<!-- 10 Services text -->
<section class="slide dark c2 r3">
  <div class="a" style="left:10px;top:150px;transform:rotate(-90deg);transform-origin:0 0;font-size:30px;font-weight:700;color:#1c1c1f;letter-spacing:1px">BRENVIK</div>
  <div class="photo" role="img" aria-label="Line drawing of a dispensing machine" style="left:222px;top:0;width:60px;height:140px;background:linear-gradient(180deg,#18181b,#101012)"></div>
  <div class="a" style="left:24px;top:13px;font-size:15px;letter-spacing:.4px">SERVICES</div>
  <div class="a tiny cols" style="left:73px;top:38px;width:64px"><p>A wonderful serenity has taken of my entire soul, like these sweet mornings of spring which I enjoy with my whole heart. I am alone, and feel the charm of existence in this spot, which was</p><p>created for the bliss of souls like mine. I am so happy, my dear friend, so absorbed in the exquisite</p><p>created for the bliss of souls like mine. I am so happy, my dear friend, so absorbed in the exquisite created for the bliss of souls like mine. I am so happy, my dear friend, so absorbed i</p></div>
  <div class="a tiny cols" style="left:145px;top:11px;width:64px"><p>A wonderful serenity has taken of my entire soul, like these sweet mornings of spring which I enjoy with my whole heart. I am alone, and feel the charm of existence in this spot, which was</p><p>created for the bliss of souls like mine. I am so happy, my dear friend, so absorbed in the exquisite</p><p>created for the bliss of souls like mine. I am so happy, my dear friend, so absorbed in the exquisite created for the bliss of souls like mine. I am so happy, my dear friend, so absorbed in the exquisite. I am so happy, my dear</p></div>
  <div class="foot"><span class="l" style="color:#fff">Brenvik Systems</span><span class="mark"><i></i>BRENVIK</span><span class="r" style="color:#fff">Presentation</span></div>
  <div class="pnum">10</div>
</section>

<!-- 11 Image + text -->
<section class="slide c3 r3">
  <div class="a kicker" style="left:29px;top:24px">Vision and<br>Missions</div>
  <div class="a desc" style="left:29px;top:38px">Description here</div>
  <div class="a title" style="left:29px;top:48px;font-size:15px">PURPOSE<br>&amp; GOALS</div>
  <div class="a tiny" style="left:29px;top:93px;width:78px;color:#aaa">A wonderful serenity has taken of my entire soul, like these sweet mornings of spring which I enjoy with my whole heart. I am alone, and feel the charm of existence in this spot, which</div>
  <svg class="a" style="left:5px;top:45px" width="18" height="90"><line x1="9" y1="2" x2="9" y2="80" stroke="#666" stroke-width=".5"/><path d="M7.5 5 9 2 10.5 5" fill="none" stroke="#666" stroke-width=".5"/><circle cx="9" cy="80" r="8" fill="none" stroke="#666" stroke-width=".5"/></svg>
  <div class="photo" role="img" aria-label="Cleanroom with glass-walled production machines" style="left:121px;top:0;width:92px;height:157px;background:linear-gradient(180deg,#e4e7ea,#9aa3ac 55%,#4d545b)"></div>
  <div class="a" style="left:213px;top:0;width:69px;height:157px;background:var(--ink)"></div>
  <div class="a" style="left:225px;top:30px;width:5px;height:4px;border:.6px solid #fff;border-radius:1px"></div>
  <div class="a" style="left:225px;top:40px;font-size:3.4px;color:#fff;letter-spacing:.3px;line-height:1.3">INSERT TITLE<br>HERE</div>
  <div class="a tiny" style="left:225px;top:52px;width:45px">Lorem ipsum dolor sit elit, consect lorem adipiscing. Lorem ipsum dolor sit elit</div>
  <div class="a" style="left:225px;top:94px;width:5px;height:4px;border:.6px solid #fff;border-radius:1px"></div>
  <div class="a" style="left:225px;top:104px;font-size:3.4px;color:#fff;letter-spacing:.3px;line-height:1.3">INSERT TITLE<br>HERE</div>
  <div class="a tiny" style="left:225px;top:116px;width:45px">Lorem ipsum dolor sit elit, consect lorem adipiscing. Lorem ipsum dolor sit elit</div>
  <div class="a tiny" style="left:30px;top:144px">Brenvik Systems</div>
  <div class="a mark" style="left:130px;top:144px;font-size:5px;color:#fff"><i style="width:4px;height:4px"></i>BRENVIK</div>
  <div class="a tiny" style="left:233px;top:144px;color:#fff">Presentation</div>
  <div class="pnum">11</div>
</section>

<!-- 12 Three step band -->
<section class="slide dark c4 r3">
  <div class="a" style="left:0;top:0;width:282px;height:46px;background:#fff"></div>
  <div class="a title" style="left:19px;top:18px;font-size:16px">PURPOSE &amp; GOALS</div>
  <div class="photo" role="img" aria-label="Macro view of a blue glowing wafer edge" style="left:0;top:46px;width:282px;height:58px;background:radial-gradient(ellipse at 40% 100%,#9fe3f5 0,#2d7fa5 35%,#1a2a6b 65%,#0e1540)"></div>
  <div class="a" style="left:28px;top:101px;width:222px;height:.5px;background:#fff"></div>
  <div class="a" style="left:29px;top:98px;display:grid;grid-template-columns:84px 84px 60px;width:240px">
    <div><span class="num">1</span><div class="item-t">TITLE HERE</div><div class="tiny" style="width:58px">Lorem ipsum dolor sit elit, consect lorem adipiscing lorem ipsum dolor sit</div></div>
    <div><span class="num">2</span><div class="item-t">TITLE HERE</div><div class="tiny" style="width:58px">Lorem ipsum dolor sit elit, consect lorem adipiscing lorem ipsum dolor sit</div></div>
    <div><span class="num">3</span><div class="item-t">TITLE HERE</div><div class="tiny" style="width:58px">Lorem ipsum dolor sit elit, consect lorem adipiscing lorem ipsum dolor sit</div></div>
  </div>
  <div class="foot"><span class="l" style="color:#fff">Brenvik Systems</span><span class="mark"><i></i>BRENVIK</span><span class="r" style="color:#fff">Presentation</span></div>
  <div class="pnum">12</div>
</section>

<!-- 13 Image left four items -->
<section class="slide c1 r4">
  <div class="photo" role="img" aria-label="Silver needle over a wafer on a white pedestal" style="left:0;top:0;width:141px;height:142px;background:linear-gradient(180deg,#f2f2f3,#d7d8da 60%,#eeeeef)"></div>
  <div class="a desc" style="left:162px;top:9px">Description here</div>
  <div class="a title" style="left:162px;top:20px;font-size:15px">PURPOSE<br>&amp; GOALS</div>
  <div class="a" style="left:165px;top:66px;display:grid;grid-template-columns:51px 51px;row-gap:10px">
    <div><span class="num">1</span><div class="item-t">TITLE HERE</div><div class="tiny" style="width:44px">Lorem ipsum dolor sit elit, consect lorem nisi. Lorem ipsum</div></div>
    <div><span class="num">2</span><div class="item-t">TITLE HERE</div><div class="tiny" style="width:44px">Lorem ipsum dolor sit elit, consect lorem nisi. Lorem ipsum</div></div>
    <div><span class="num">3</span><div class="item-t">TITLE HERE</div><div class="tiny" style="width:44px">Lorem ipsum dolor sit elit, consect lorem nisi. Lorem ipsum</div></div>
    <div><span class="num">4</span><div class="item-t">TITLE HERE</div><div class="tiny" style="width:44px">Lorem ipsum dolor sit elit, consect lorem nisi. Lorem ipsum</div></div>
  </div>
  <div class="foot"><span class="l">Brenvik Systems</span><span class="mark"><i></i>BRENVIK</span><span class="r">Presentation</span></div>
  <div class="pnum">13</div>
</section>

<!-- 14 Dark + portrait -->
<section class="slide dark c2 r4">
  <div class="photo" role="img" aria-label="Engineer in a lab coat working at a cleanroom machine" style="left:142px;top:0;width:140px;height:157px;background:linear-gradient(120deg,#2b2e35,#7b7f86 45%,#c9c6c0 70%,#8b8d92)"></div>
  <div class="a desc" style="left:24px;top:9px">Description here</div>
  <div class="a title" style="left:24px;top:20px;font-size:15px">PURPOSE<br>&amp; GOALS</div>
  <div class="a" style="left:27px;top:66px;display:grid;grid-template-columns:51px 51px;row-gap:10px">
    <div><span class="num">1</span><div class="item-t">TITLE HERE</div><div class="tiny" style="width:44px">Lorem ipsum dolor sit elit, consect lorem nisi. Lorem ipsum</div></div>
    <div><span class="num">2</span><div class="item-t">TITLE HERE</div><div class="tiny" style="width:44px">Lorem ipsum dolor sit elit, consect lorem nisi. Lorem ipsum</div></div>
    <div><span class="num">3</span><div class="item-t">TITLE HERE</div><div class="tiny" style="width:44px">Lorem ipsum dolor sit elit, consect lorem nisi. Lorem ipsum</div></div>
    <div><span class="num">4</span><div class="item-t">TITLE HERE</div><div class="tiny" style="width:44px">Lorem ipsum dolor sit elit, consect lorem nisi. Lorem ipsum</div></div>
  </div>
  <div class="foot" style="border:none"><span class="l" style="color:#fff">Brenvik Systems</span><span class="mark"><i></i>BRENVIK</span><span class="r" style="color:#fff">Presentation</span></div>
  <div class="pnum">14</div>
</section>

<!-- 15 Title + dark text panel -->
<section class="slide c3 r4">
  <svg class="a" style="left:23px;top:18px" width="95" height="20"><circle cx="10" cy="10" r="9" fill="none" stroke="#666" stroke-width=".5"/><line x1="10" y1="10" x2="93" y2="10" stroke="#555" stroke-width=".5"/><path d="M90 8.5 93 10 90 11.5" fill="none" stroke="#555" stroke-width=".5"/></svg>
  <div class="a kicker" style="left:25px;top:53px">Vision and<br>Missions</div>
  <div class="a desc" style="left:25px;top:67px">Description here</div>
  <div class="a title" style="left:25px;top:77px;font-size:15px">PURPOSE<br>&amp; GOALS</div>
  <div class="a" style="left:127px;top:27px;width:155px;height:130px;background:var(--ink)"></div>
  <div class="a tiny cols" style="left:140px;top:38px;width:62px"><p>A wonderful serenity has taken of my entire soul, like these sweet mornings of spring which I enjoy with my whole heart. I am alone, and feel the charm of existence in this spot, which was</p><p>created for the bliss of souls like mine. I am so happy, my dear friend, so absorbed in the exquisite</p><p>created for the bliss of souls like mine. I am so happy, my dear friend, so absorbed in the exquisite created for the bliss of souls like mine. I am so happy, my dear friend, so absorbed i</p></div>
  <div class="a tiny cols" style="left:208px;top:38px;width:62px"><p>A wonderful serenity has taken of my entire soul, like these sweet mornings of spring which I enjoy with my whole heart. I am alone, and feel the charm of existence in this spot, which was</p><p>created for the bliss of souls like mine. I am so happy, my dear friend, so absorbed in the exquisite</p><p>created for the bliss of souls like mine. I am so happy, my dear friend, so absorbed in the exquisite created for the bliss of souls like mine. I am so happy, my dear friend, so absorbed i</p></div>
  <div class="a tiny" style="left:22px;top:144px">Brenvik Systems</div>
  <div class="a tiny" style="left:232px;top:144px;color:#fff">Presentation</div>
  <div class="pnum">15</div>
</section>

<!-- 16 Timeline list -->
<section class="slide dark c4 r4">
  <div class="photo" role="img" aria-label="Conical dispensing nozzle above a glowing disc" style="left:10px;top:0;width:115px;height:80px;background:radial-gradient(ellipse at 50% 75%,#f4f6ff 0,#b9c2e8 25%,#3b3f4c 55%,#0e0e10 80%)"></div>
  <div class="a desc" style="left:31px;top:90px">Description here</div>
  <div class="a" style="left:31px;top:98px;font-size:15px;font-weight:600;line-height:1.12">PURPOSE<br>&amp; GOALS</div>
  <div class="a" style="left:130px;top:15px;width:2px;height:108px;background:transparent"></div>
  <div class="a" style="left:130px;top:14px;width:140px">
    <div style="display:flex;gap:6px;height:16.5px"><span style="font-size:2.6px;border:.5px solid var(--blue);padding:0 1px;height:4px;line-height:4px">01</span><div class="tiny">Brenvik Systems has recently undergone a complete rebranding, including a new logo, website, and visual identity.</div></div>
    <div style="display:flex;gap:6px;height:16.5px"><span style="font-size:2.6px;border:.5px solid var(--blue);padding:0 1px;height:4px;line-height:4px">02</span><div class="tiny">Brenvik Systems has recently undergone a complete rebranding, including a new logo, website, and visual identity.</div></div>
    <div style="display:flex;gap:6px;height:16.5px"><span style="font-size:2.6px;border:.5px solid var(--blue);padding:0 1px;height:4px;line-height:4px">03</span><div class="tiny">Brenvik Systems has recently undergone a complete rebranding, including a new logo, website, and visual identity.</div></div>
    <div style="display:flex;gap:6px;height:16.5px"><span style="font-size:2.6px;border:.5px solid var(--blue);padding:0 1px;height:4px;line-height:4px">01</span><div class="tiny">Brenvik Systems has recently undergone a complete rebranding, including a new logo, website, and visual identity.</div></div>
    <div style="display:flex;gap:6px;height:16.5px"><span style="font-size:2.6px;border:.5px solid var(--blue);padding:0 1px;height:4px;line-height:4px">02</span><div class="tiny">Brenvik Systems has recently undergone a complete rebranding, including a new logo, website, and visual identity.</div></div>
    <div style="display:flex;gap:6px;height:16.5px"><span style="font-size:2.6px;border:.5px solid var(--blue);padding:0 1px;height:4px;line-height:4px">03</span><div class="tiny">Brenvik Systems has recently undergone a complete rebranding, including a new logo, website, and visual identity.</div></div>
  </div>
  <svg class="a" style="left:128px;top:112px" width="130" height="16"><circle cx="8" cy="8" r="7" fill="none" stroke="#aaa" stroke-width=".5"/><line x1="8" y1="8" x2="128" y2="8" stroke="#aaa" stroke-width=".5"/><path d="M125 6.5 128 8 125 9.5" fill="none" stroke="#aaa" stroke-width=".5"/></svg>
  <div class="foot" style="border:none"><span class="l" style="color:#fff">Brenvik Systems</span><span class="mark"><i></i>BRENVIK</span><span class="r" style="color:#fff">Presentation</span></div>
  <div class="pnum">16</div>
</section>

<!-- 17 Collage -->
<section class="slide c1 r5">
  <div class="a" style="left:0;top:0;width:282px;height:68px;background:var(--ink)"></div>
  <div class="a desc" style="left:22px;top:12px;color:#ccc">Description here</div>
  <div class="a" style="left:22px;top:20px;font-size:15px;font-weight:600;line-height:1.12;color:#fff">PURPOSE<br>&amp; GOALS</div>
  <div class="photo" role="img" aria-label="Macro of a patterned wafer surface" style="left:162px;top:33px;width:63px;height:34px;background:linear-gradient(135deg,#c9cacd,#8d9095)"></div>
  <div class="photo" role="img" aria-label="Polished discs on a grey surface" style="left:227px;top:10px;width:55px;height:57px;background:linear-gradient(135deg,#e6e6e6,#9c9ea2)"></div>
  <div class="photo" role="img" aria-label="Dark machine interior with wafer stage" style="left:103px;top:70px;width:57px;height:64px;background:linear-gradient(135deg,#2a2c31,#5c5f66)"></div>
  <div class="photo" role="img" aria-label="Cleanroom production line" style="left:173px;top:70px;width:50px;height:64px;background:linear-gradient(180deg,#dfe3e6,#8a939b)"></div>
  <div class="photo" role="img" aria-label="Gloved hands holding a wafer" style="left:227px;top:70px;width:55px;height:64px;background:linear-gradient(135deg,#f3f3f3,#d7b9a3 55%,#bfc2c6)"></div>
  <div class="a" style="left:20px;top:79px;width:80px">
    <div style="display:flex;gap:5px;height:18px"><span class="num">1</span><div><div class="item-t" style="margin:0">TITLE HERE</div><div class="tiny">Lorem ipsum dolor sit elit, consect lorem nisi</div></div></div>
    <div style="display:flex;gap:5px;height:18px"><span class="num">1</span><div><div class="item-t" style="margin:0">TITLE HERE</div><div class="tiny">Lorem ipsum dolor sit elit, consect lorem nisi</div></div></div>
    <div style="display:flex;gap:5px;height:18px"><span class="num">1</span><div><div class="item-t" style="margin:0">TITLE HERE</div><div class="tiny">Lorem ipsum dolor sit elit, consect lorem nisi</div></div></div>
  </div>
  <div class="foot"><span class="l">Brenvik Systems</span><span class="mark"><i></i>BRENVIK</span><span class="r">Presentation</span></div>
  <div class="pnum">17</div>
</section>

<!-- 18 Quotes -->
<section class="slide c2 r5">
  <div class="a" style="left:0;top:21px;width:104px;height:115px;background:var(--ink)"></div>
  <div class="a" style="left:271px;top:21px;width:11px;height:115px;background:var(--ink)"></div>
  <div class="a desc" style="left:13px;top:52px;color:#ccc">Description here</div>
  <div class="a" style="left:13px;top:60px;font-size:15px;font-weight:600;line-height:1.12;color:#fff">PURPOSE<br>&amp; GOALS</div>
  <svg class="a" style="left:30px;top:105px" width="100" height="20"><circle cx="10" cy="10" r="9" fill="none" stroke="#888" stroke-width=".5"/><line x1="10" y1="10" x2="98" y2="10" stroke="#888" stroke-width=".5"/></svg>
  <div class="a" style="left:112px;top:26px;font-size:20px;color:#aaa;font-family:Georgia,serif">“</div>
  <div class="a" style="left:119px;top:52px;width:140px;font-size:2.8px;color:#444">
    <div style="display:flex;height:28px"><span style="width:47px">IVO MARTEN</span><span class="tiny" style="width:93px">Presentations are communication tools that can be used as demonstrations, lectures, speeches, reports, and more.</span></div>
    <div style="display:flex;height:25px"><span style="width:47px">SELMA DRAY</span><span class="tiny" style="width:93px">Presentations are communication tools that can be used as demonstrations, lectures, speeches, reports, and more.</span></div>
    <div style="display:flex"><span style="width:47px">JORAN VICE</span><span class="tiny" style="width:93px">Presentations are communication tools that can be used as demonstrations, lectures, speeches, reports, and more.</span></div>
  </div>
  <div class="foot"><span class="l">Brenvik Systems</span><span class="mark"><i></i>BRENVIK</span><span class="r">Presentation</span></div>
  <div class="pnum">18</div>
</section>

<!-- 19 Chart with render -->
<section class="slide c3 r5">
  <div class="a" style="left:175px;top:15px;width:107px;height:124px;background:var(--ink)"></div>
  <div class="photo" role="img" aria-label="Rendered blue cylindrical lens with white rim" style="left:110px;top:15px;width:95px;height:124px;background:radial-gradient(ellipse at 70% 50%,#fff 0,#3a59ff 18%,#1f3fe6 35%,#cfd0d4 60%,#f4f4f5 80%)"></div>
  <div class="a kicker" style="left:18px;top:34px">Vision and<br>Missions</div>
  <div class="a desc" style="left:18px;top:48px">Description here</div>
  <div class="a title" style="left:18px;top:58px;font-size:15px">Data/Chart<br>Slide</div>
  <div class="a tiny" style="left:19px;top:95px;width:55px">Lorem ipsum dolor sit elit, consect lorem adipiscing lorem ipsum dolor</div>
  <div class="a" style="left:18px;top:117px;font-size:11px;color:var(--blue)">→</div>
  <div class="a" style="left:215px;top:32px;width:10px;height:4px;border-radius:1px;background:var(--blue)"></div>
  <div class="a tiny" style="left:215px;top:39px;width:40px">Lorem ipsum dolor sit elit, consect lorem</div>
  <div class="a" style="left:215px;top:66px;width:10px;height:4px;border-radius:1px;background:#3c5bb8"></div>
  <div class="a tiny" style="left:215px;top:73px;width:40px">Lorem ipsum dolor sit elit, consect lorem</div>
  <div class="a" style="left:215px;top:101px;width:10px;height:4px;border-radius:1px;background:#fff"></div>
  <div class="a tiny" style="left:215px;top:108px;width:40px">Lorem ipsum dolor sit elit, consect lorem</div>
  <div class="foot"><span class="l">Brenvik Systems</span><span class="mark"><i></i>BRENVIK</span><span class="r">Presentation</span></div>
  <div class="pnum">19</div>
</section>

<!-- 20 Bar chart -->
<section class="slide dark c4 r5">
  <div class="a" style="left:17px;top:13px;font-size:14px;font-weight:600">Data/Chart Slide</div>
  <div class="a kicker" style="left:242px;top:19px;text-align:center;color:var(--blue-soft)">Vision and<br>Missions</div>
  <div class="a" style="left:16px;top:43px;width:117px;height:38px;background:var(--blue)">
    <div class="a" style="left:10px;top:8px;font-size:9px">89<span style="font-size:4px"> %</span></div>
    <div class="a" style="left:44px;top:9px;font-size:4.6px">Trend design 2020</div>
    <div class="a tiny" style="left:44px;top:15px;color:#dfe4ff">A wonderful serenity</div>
    <div class="a" style="left:108px;top:4px;font-size:4px">A</div>
    <div class="a" style="left:6px;top:24px;width:104px;height:1.3px;background:#6d83ff"></div>
    <div class="a" style="left:6px;top:24px;width:92px;height:1.3px;background:#fff"></div>
    <div class="a tiny" style="left:6px;top:28px;color:#dfe4ff">64% Progress</div>
    <div class="a tiny" style="left:100px;top:28px;color:#dfe4ff">Empty</div>
  </div>
  <div class="a" style="left:16px;top:88px;width:117px;height:38px;background:var(--blue)">
    <div class="a" style="left:10px;top:8px;font-size:9px">65<span style="font-size:4px"> %</span></div>
    <div class="a" style="left:44px;top:9px;font-size:4.6px">Trend design 2019</div>
    <div class="a tiny" style="left:44px;top:15px;color:#dfe4ff">A wonderful serenity</div>
    <div class="a" style="left:108px;top:4px;font-size:4px">B</div>
    <div class="a" style="left:6px;top:24px;width:104px;height:1.3px;background:#6d83ff"></div>
    <div class="a" style="left:6px;top:24px;width:62px;height:1.3px;background:#fff"></div>
    <div class="a tiny" style="left:6px;top:28px;color:#dfe4ff">64% Progress</div>
    <div class="a tiny" style="left:65px;top:28px;color:#dfe4ff">Empty</div>
  </div>
  <svg class="a" style="left:140px;top:40px" width="135" height="100" font-family="Montserrat,Arial,sans-serif">
    <g font-size="3.6" fill="#ddd" text-anchor="end">
      <text x="12" y="3">100%</text><text x="12" y="10.8">90%</text><text x="12" y="18.6">80%</text><text x="12" y="26.4">70%</text><text x="12" y="34.2">60%</text><text x="12" y="42">50%</text><text x="12" y="49.8">40%</text><text x="12" y="57.6">30%</text><text x="12" y="65.4">20%</text><text x="12" y="73.2">10%</text><text x="12" y="81">0%</text>
    </g>
    <line x1="15" y1="80" x2="130" y2="80" stroke="#555" stroke-width=".4"/>
    <g fill="#2b4df0">
      <rect x="22" y="14" width="4.5" height="66"/><rect x="47" y="10" width="4.5" height="70"/><rect x="72" y="12" width="4.5" height="68"/><rect x="97" y="10" width="4.5" height="70"/>
    </g>
    <g fill="#3556ff">
      <rect x="28" y="32" width="4.5" height="48"/><rect x="53" y="27" width="4.5" height="53"/><rect x="78" y="34" width="4.5" height="46"/><rect x="103" y="28" width="4.5" height="52"/>
    </g>
    <g font-size="3.6" fill="#ddd" text-anchor="middle">
      <text x="27" y="87">FEBRUARY</text><text x="52" y="87">MARCH</text><text x="77" y="87">APRIL</text><text x="102" y="87">MAY</text>
      <text x="60" y="94">■ Data A&#160;&#160;■ Data B</text>
    </g>
  </svg>
  <div class="foot" style="border:none"><span class="l" style="color:#fff">Brenvik Systems</span><span class="mark"><i></i>BRENVIK</span><span class="r" style="color:#fff">Presentation</span></div>
  <div class="pnum">20</div>
</section>

<!-- 21 Table -->
<section class="slide c1 r6">
  <div class="a" style="left:0;top:0;width:282px;height:42px;background:var(--ink)"></div>
  <div class="a" style="left:0;top:11px;width:282px;text-align:center;font-size:14px;font-weight:600;color:#fff">Data/Chart Slide</div>
  <svg class="a" style="left:0;top:42px" width="282" height="115" font-family="Montserrat,Arial,sans-serif">
    <rect x="0" y="0" width="282" height="13" fill="#2342ea"/>
    <g font-size="3" fill="#fff" font-weight="600">
      <text x="12" y="5">Duis aute lure lorem</text><text x="12" y="9">dolor in reprehendrit</text>
    </g>
    <g font-size="3" fill="#fff" font-weight="600" text-anchor="middle">
      <text x="84" y="5">Title goes</text><text x="84" y="9">here</text>
      <text x="113" y="5">Title goes</text><text x="113" y="9">here</text>
      <text x="143" y="5">Title goes</text><text x="143" y="9">here</text>
      <text x="172" y="5">Title goes</text><text x="172" y="9">here</text>
      <text x="201" y="5">Title goes</text><text x="201" y="9">here</text>
      <text x="231" y="5">Title goes</text><text x="231" y="9">here</text>
      <text x="260" y="5">Title goes</text><text x="260" y="9">here</text>
    </g>
    <rect x="0" y="29" width="282" height="16" fill="#efeff0"/>
    <rect x="0" y="61" width="282" height="16" fill="#efeff0"/>
    <g stroke="#ddd" stroke-width=".4">
      <line x1="70" y1="13" x2="70" y2="93"/><line x1="99" y1="13" x2="99" y2="93"/><line x1="128" y1="13" x2="128" y2="93"/><line x1="157" y1="13" x2="157" y2="93"/><line x1="186" y1="13" x2="186" y2="93"/><line x1="216" y1="13" x2="216" y2="93"/><line x1="245" y1="13" x2="245" y2="93"/>
    </g>
    <g font-size="2.4" fill="#777">
      <text x="18" y="22">Duis aute lure lorem dolor in</text>
      <text x="18" y="38">Duis aute lure lorem dolor</text>
      <text x="18" y="54">Duis aute lure lorem dolor in</text>
      <text x="18" y="70">Duis aute lure lorem dolor</text>
      <text x="18" y="86">Duis aute lure lorem dolor in</text>
    </g>
    <g font-size="3.4" font-weight="700" fill="#222" text-anchor="middle">
      <text x="84" y="23">8.534</text><text x="143" y="23">8.534</text><text x="172" y="23">8.534</text>
      <text x="113" y="39">8.534</text><text x="143" y="39">592</text><text x="231" y="39">14.524</text><text x="260" y="39">8.534</text>
      <text x="113" y="55">9.523</text><text x="172" y="55">8.534</text><text x="201" y="55">18.524</text><text x="231" y="55">8.534</text>
      <text x="143" y="87">8.534</text><text x="201" y="87">8.534</text><text x="260" y="87">924</text>
    </g>
    <g font-size="2.2" fill="#888" text-anchor="middle">
      <text x="201" y="22">Some text</text><text x="84" y="54">Some text</text><text x="143" y="54"></text>
      <text x="260" y="54">Some text</text><text x="113" y="70">Some text</text><text x="143" y="70"></text>
      <text x="172" y="70">Some text</text><text x="260" y="70">Some text</text><text x="84" y="86">Some text</text><text x="231" y="86">Some text</text>
    </g>
    <g fill="none" stroke="#2342ea" stroke-width="1">
      <path d="M109 20l3 3 5-6"/><path d="M227 20l3 3 5-6"/><path d="M80 36l3 3 5-6"/><path d="M168 36l3 3 5-6"/>
      <path d="M139 68l3 3 5-6"/><path d="M197 68l3 3 5-6"/><path d="M256 52l3 3 5-6"/><path d="M109 84l3 3 5-6"/><path d="M139 52l3 3 5-6"/>
    </g>
    <g stroke="#888" stroke-width=".5">
      <path d="M258 19l4 4M262 19l-4 4"/><path d="M199 35l4 4M203 35l-4 4"/><path d="M141 51l4 4M145 51l-4 4"/>
      <path d="M82 67l4 4M86 67l-4 4"/><path d="M229 67l4 4M233 67l-4 4"/><path d="M170 83l4 4M174 83l-4 4"/>
    </g>
    <rect x="0" y="93" width="282" height="22" fill="#0e0e10"/>
  </svg>
  <div class="a tiny" style="left:22px;top:144px;color:#fff">Brenvik Systems</div>
  <div class="a mark" style="left:130px;top:143px;font-size:5px;color:#fff"><i style="width:4px;height:4px"></i>BRENVIK</div>
  <div class="a tiny" style="left:232px;top:144px;color:#fff">Presentation</div>
  <div class="pnum" style="top:132px">21</div>
</section>

<!-- 22 Donuts -->
<section class="slide c2 r6" style="left:313px;width:284px">
  <div class="a" style="left:129px;top:0;width:155px;height:157px;background:var(--ink)"></div>
  <div class="a" style="left:85px;top:17px;font-size:12px;color:var(--blue)">→</div>
  <div class="a title" style="left:19px;top:38px;font-size:15px">Data/<br>Chart Slide</div>
  <div class="a tiny" style="left:21px;top:80px;width:85px;color:#bbb">Lorem ipsum dolor sit elit, consect lorem adipiscing nisi aute. elit, sit elit, sit elit, consect lorem adipiscing nisi deposit. Ipsum sit elit. Lorem ipsum dolor sit elit. Lorem</div>
  <div class="a" style="left:46px;top:108px;width:11px;height:4px;border-radius:1.5px;background:var(--blue)"></div>
  <div class="a" style="left:83px;top:108px;width:11px;height:4px;border-radius:1.5px;background:var(--blue-soft)"></div>
  <div class="a tiny" style="left:46px;top:115px;width:28px">Lorem ipsum dolor sit elit, consect</div>
  <div class="a tiny" style="left:83px;top:115px;width:28px">Lorem ipsum dolor sit elit, consect</div>
  <svg class="a" style="left:163px;top:25px" width="46" height="46"><circle cx="23" cy="23" r="16" fill="none" stroke="#c9c9cc" stroke-width="10"/><circle cx="23" cy="23" r="16" fill="none" stroke="#1f3fe6" stroke-width="10" stroke-dasharray="70 31" transform="rotate(-90 23 23)"/></svg>
  <div class="a" style="left:218px;top:26px;font-size:11px;color:#fff">28%</div>
  <div class="a tiny" style="left:218px;top:42px;width:42px">Lorem ipsum dolor sit elit, consect lorem adipiscing lorem ipsum</div>
  <svg class="a" style="left:163px;top:92px" width="46" height="46"><circle cx="23" cy="23" r="16" fill="none" stroke="#c9c9cc" stroke-width="10"/><circle cx="23" cy="23" r="16" fill="none" stroke="#8196ff" stroke-width="10" stroke-dasharray="55 46" transform="rotate(-90 23 23)"/></svg>
  <div class="a" style="left:218px;top:95px;font-size:9px;color:#fff">22%</div>
  <div class="a tiny" style="left:218px;top:109px;width:42px">Lorem ipsum dolor sit elit, consect lorem</div>
</section>

</body>
</html>
```